Luxury Real Estate Website, Midwest, United States

We need web design services for a luxury website. We need IDX Integration with our MLS. We want this to be a very simple website with amazing graphics. We want it to link up with our Mail mascot placeholder account in order to generate leads through a "More Information" Pop up on the main page. We want the main page to be covered with one large graphic that is a rolling slideshow of active listings of $400,000 and up from the IDX Integration. We need this website to give a very exclusive and sleek look. Lots of black is good... I will upload our logos in Black and Silver. We will also need an "About" page that we are going to call "Qeno Info". We want our graphics to be extremely impressive. Keep in mind, we are a company in the Midwest of the United States, and our real estate has a different look than homes in California or Florida. We need graphics that are realistic for the Midwest, yet still high-end.
Target Market(s)
Luxury Homeowners in the Midwest United States. The graphics needs to be pristine.
Industry/Entity Type
Real Estate
Coding
Coded - Design and coding required
Number of Pages Required
3 page
Requirements
Must have
- Large graphics with IDX Integration. The photos of real estate need to represent real estate that is common in the Midwest, United States. We also need Mail mascot placeholder integration. We need a pop up that is titled "My Free Market Analysis" that makes them fill out a contact form asking for Full Name, Email Address, Phone Number and Address. This needs to be a pop up on the front page and will integrate with our Mail mascot placeholder account. We also need a page called "About Qe No Home". And another page where clients can download informational PDFs. The main component needs to be a front page search engine connected with the IDX to access active listings from our MLS. I attached our logos and a sample front page of a website. I would love for ours to look similar.
Nice to have
- Lake House photos on midwest lakes are a plus.
Should not have
- Should not have clutter. This website needs to be clean, luxurious and exclusive.

```html
<!DOCTYPE html>
<html lang="en">
<head>
<meta charset="utf-8">
<title>Qeno Realty Group — My Free Market Analysis</title>
<link rel="stylesheet" href="https://fonts.googleapis.com/css2?family=Cinzel:wght@400;600;700&family=Open+Sans:wght@400;600&display=swap">
<style>
:root{
  --page:#2a2a2a;
  --header:#161616;
  --footer:#101010;
  --ink:#1a1a1a;
  --paper:#ffffff;
  --frame:#c9d8ea;
  --accent:#b5cbe3;
  --field-line:#d6d6d6;
  --button:#6f6f6f;
  --veil:rgba(0,0,0,.78);
  --photo-home:linear-gradient(180deg,#8fa6bd 0%,#b4bfc9 30%,#7a6e62 48%,#5d534a 62%,#5f6f45 78%,#46552f 100%);
  --photo-lake:linear-gradient(180deg,#9db3c8 0%,#c3ccd3 32%,#6e6a60 50%,#4f6478 66%,#3e5368 100%);
  --photo-brick:linear-gradient(180deg,#c9d1d8 0%,#d8dcdf 28%,#8d7465 46%,#6f5a4d 64%,#6c7752 80%,#56623f 100%);
}
*{box-sizing:border-box;margin:0;padding:0}
html,body{width:1200px;height:2917px;overflow:hidden}
body{position:relative;background:var(--page);font-family:"Open Sans",Arial,sans-serif;color:#fff}
.abs{position:absolute}

/* page beneath the popup */
.site-header{left:0;top:0;width:1200px;height:97px;background:var(--header)}
.brand{left:117px;top:28px;font-weight:600;font-size:28px;letter-spacing:2px;color:#ddd}
.main-nav{left:380px;top:36px;display:flex;gap:46px;font-size:15px;color:#ccc}
.sign-in{left:982px;top:27px;width:117px;height:39px;border:2px solid #ccc;border-radius:20px;font-size:15px;color:#ccc;display:flex;align-items:center;justify-content:center}
.hero{left:0;top:97px;width:1200px;height:500px;background:var(--photo-home)}
.hero-caption{left:0;top:532px;width:1200px;text-align:center;font-family:"Cinzel",serif;font-size:26px;letter-spacing:6px;color:#ddd}

.section-title{font-family:"Cinzel",serif;font-size:40px;font-weight:700;color:#111;letter-spacing:1px;white-space:nowrap}
.section-title span{color:#444;font-weight:400}
.about-title{left:405px;top:700px}
.about-text{left:117px;top:800px;width:447px;font-size:16px;line-height:38px;color:#555}
.about-rule{left:611px;top:788px;width:6px;height:128px;border:2px solid #111;border-radius:3px}
.about-photo{left:661px;top:690px;width:434px;height:318px;background:var(--photo-brick)}
.pill{border-radius:22px;background:#444;color:#ddd;font-size:15px;display:flex;align-items:center;justify-content:center}
.about-more{left:832px;top:1138px;width:218px;height:43px}

.listings-title{left:0;top:1308px;width:1200px;text-align:center}
.listing-card{top:1400px;width:300px}
.listing-photo{width:300px;height:214px}
.listing-name{margin-top:24px;font-size:17px;font-weight:400;color:#333}
.listing-desc{margin-top:6px;font-size:14px;color:#444}
.listing-meta{margin-top:24px;display:flex;justify-content:space-between;font-size:14px;color:#444}

.contact-title{left:0;top:2375px;width:1200px;text-align:center}
.contact-field{left:160px;width:880px;border-bottom:1px solid #3a3a3a;font-size:15px;color:#444;padding-bottom:10px}
.contact-send{left:517px;top:2669px;width:166px;height:42px;background:#111}
.contact-info{left:230px;top:2742px;display:flex;align-items:center;gap:14px;font-size:15px;color:#444}
.social{display:flex;gap:24px;margin-left:80px}
.social i{display:block;width:28px;height:28px;border-radius:50%;background:#1a1a1a}
.site-footer{left:0;top:2865px;width:1200px;height:52px;background:var(--footer);text-align:center;line-height:52px;font-size:13px;color:#333}

/* dimming veil */
.veil{left:0;top:0;width:1200px;height:2917px;background:var(--veil)}

/* popup */
.popup{left:185px;top:136px;width:828px;height:395px;background:var(--paper);border:10px solid var(--frame)}
.popup-close{left:984px;top:117px;width:54px;height:54px}
.mascot{left:222px;top:196px;width:238px;height:264px;border-radius:14px;background:linear-gradient(160deg,#e9e4df 0%,#b98a5e 30%,#7a4d2b 58%,#2f5597 80%,#24447c 100%)}
.popup-title{left:496px;top:220px;font-family:"Cinzel",serif;font-weight:700;font-size:32px;line-height:1;color:var(--ink);white-space:nowrap}
.popup-title .accent{color:var(--accent)}
.field{width:237px;height:41px;border:1px solid var(--field-line);font-size:13px;color:#6a6a6a;padding:0 20px;display:flex;align-items:center}
.submit{left:496px;top:401px;width:121px;height:42px;border-radius:21px;background:var(--button);color:#fff;font-size:17px;font-weight:600;letter-spacing:.5px;display:flex;align-items:center;justify-content:center}
.popup-brand{right:233px;top:444px;display:flex;align-items:center;gap:10px;font-weight:600;font-size:19px;color:var(--ink);letter-spacing:.5px;white-space:nowrap}
.popup-brand i{display:block;width:14px;height:14px;background:var(--ink)}
</style>
</head>
<body>

<header class="abs site-header"></header>
<div class="abs brand">QENO</div>
<nav class="abs main-nav"><span>Home</span><span>Qeno Info</span><span>About Qe No Home</span><span>Downloads</span><span>Contact Us</span></nav>
<div class="abs sign-in">Sign In</div>

<div class="abs hero" role="img" aria-label="Slideshow photo of a Midwest luxury home listing"></div>
<div class="abs hero-caption">Midwest Luxury Homes</div>

<h2 class="abs section-title about-title">About <span>Us</span></h2>
<p class="abs about-text">We are a boutique brokerage serving lake and estate homes across the Midwest. Our team pairs local knowledge with quiet discretion, guiding every buyer and seller from the first showing to the final signature.</p>
<div class="abs about-rule"></div>
<div class="abs about-photo" role="img" aria-label="Photo of a stately brick home"></div>
<div class="abs pill about-more">Learn More</div>

<h2 class="abs section-title listings-title">Our <span>Listings</span></h2>
<article class="abs listing-card" style="left:107px">
  <div class="listing-photo" style="background:var(--photo-lake)" role="img" aria-label="Photo of a lakeside estate"></div>
  <h3 class="listing-name">Lakeside Estate</h3>
  <p class="listing-desc">Five bedrooms on two wooded acres</p>
  <div class="listing-meta"><span>$1,250,000</span><span>4,800 sq ft</span></div>
</article>
<article class="abs listing-card" style="left:451px">
  <div class="listing-photo" style="background:var(--photo-home)" role="img" aria-label="Photo of a prairie residence"></div>
  <h3 class="listing-name">Prairie Ridge Residence</h3>
  <p class="listing-desc">Four bedrooms beside the fairway</p>
  <div class="listing-meta"><span>$980,000</span><span>4,100 sq ft</span></div>
</article>
<article class="abs listing-card" style="left:794px">
  <div class="listing-photo" style="background:var(--photo-brick)" role="img" aria-label="Photo of a woodland manor"></div>
  <h3 class="listing-name">Woodland Manor</h3>
  <p class="listing-desc">Six bedrooms with a stone terrace</p>
  <div class="listing-meta"><span>$1,640,000</span><span>5,600 sq ft</span></div>
</article>

<div class="abs" style="left:0;top:1834px;width:395px;height:241px;background:var(--photo-home)" role="img" aria-label="Photo of a home with lawn"></div>
<div class="abs" style="left:403px;top:1834px;width:394px;height:241px;background:var(--photo-brick)" role="img" aria-label="Photo of a suburban home"></div>
<div class="abs" style="left:805px;top:1834px;width:395px;height:241px;background:var(--photo-home)" role="img" aria-label="Photo of a large family home"></div>
<div class="abs" style="left:0;top:2077px;width:593px;height:218px;background:var(--photo-lake)" role="img" aria-label="Photo of a lake house with pool"></div>
<div class="abs" style="left:603px;top:2077px;width:597px;height:218px;background:var(--photo-brick)" role="img" aria-label="Photo of a modern farmhouse"></div>

<h2 class="abs section-title contact-title">Contact <span>Us</span></h2>
<div class="abs contact-field" style="top:2470px">Name</div>
<div class="abs contact-field" style="top:2528px">Email</div>
<div class="abs contact-field" style="top:2596px">Message</div>
<div class="abs pill contact-send">Send Message</div>
<div class="abs contact-info">
  <svg width="16" height="22" viewBox="0 0 16 22"><rect x="1" y="1" width="14" height="20" rx="2" fill="none" stroke="#444" stroke-width="2"/><circle cx="8" cy="17" r="1.5" fill="#444"/></svg>
  <span>(555) 014-2290</span>
  <svg width="22" height="16" viewBox="0 0 22 16" style="margin-left:40px"><rect x="1" y="1" width="20" height="14" fill="none" stroke="#444" stroke-width="2"/><path d="M1 1l10 8 10-8" fill="none" stroke="#444" stroke-width="2"/></svg>
  <span>hello@qenorealty.example</span>
  <div class="social"><i></i><i></i><i></i><i></i></div>
</div>
<footer class="abs site-footer">© 2024 Qeno Realty Group. All rights reserved.</footer>

<div class="abs veil"></div>

<section class="abs popup" aria-label="My Free Market Analysis"></section>
<svg class="abs popup-close" viewBox="0 0 54 54" aria-label="Close">
  <circle cx="27" cy="27" r="24" fill="#fff" stroke="#c9d8ea" stroke-width="5"/>
  <circle cx="27" cy="27" r="15" fill="#c9d8ea"/>
  <path d="M21 21l12 12M33 21L21 33" stroke="#fff" stroke-width="4" stroke-linecap="round"/>
</svg>
<div class="abs mascot" role="img" aria-label="Mail carrier mascot illustration with a blue satchel"></div>
<h2 class="abs popup-title">My Free <span class="accent">Market Analysis</span></h2>
<div class="abs field" style="left:496px;top:282px">Full Name</div>
<div class="abs field" style="left:745px;top:282px">Email Address</div>
<div class="abs field" style="left:496px;top:335px">Phone Number</div>
<div class="abs field" style="left:745px;top:335px">Address</div>
<div class="abs submit">SUBMIT</div>
<div class="abs popup-brand"><span>Qeno Realty Group</span><i></i></div>

</body>
</html>
```